Create a memorable Stationary for Security Software Company

Velbrantix is the worldwide leader in securing the Internet. Making Internet communications and critical data secure, reliable and available everywhere has been and continues to be our ongoing vision. We are committed to staying focused on real customer needs and to developing new and innovative security solutions that redefine the security landscape.

Industry/Entity Type

Internet

Font styles to use
Serif
Sans Serif
Script

Colors
0792cd
33a6d7
85cae6

```html
<!DOCTYPE html>
<html lang="en">
<head>
<meta charset="utf-8">
<title>Velbrantix Business Cards</title>
<link href="https://fonts.googleapis.com/css2?family=Open+Sans:wght@400;600;700&display=swap" rel="stylesheet">
<style>
  :root {
    --blue-deep: #0792cd;
    --blue-mid: #33a6d7;
    --blue-light: #85cae6;
    --ink: #3a3a3a;
    --ink-soft: #555555;
    --paper: #ffffff;
    --backdrop: #eef1f3;
    --rule: #cfcfcf;
  }
  * { box-sizing: border-box; margin: 0; padding: 0; }
  html, body {
    width: 1200px; height: 1120px; overflow: hidden;
    background: var(--backdrop);
    font-family: "Open Sans", Arial, sans-serif;
  }
  .canvas {
    position: relative; width: 1200px; height: 1120px;
  }
  .card {
    position: absolute; left: 250px; width: 700px; height: 400px;
    box-shadow: 0 6px 20px rgba(0,0,0,0.15);
    overflow: hidden;
  }
  .card-front { top: 110px; background: var(--blue-light); }
  .card-back { top: 610px; background: var(--paper); }

  .brand {
    display: flex; align-items: center; gap: 16px;
  }
  .brand-mark {
    width: 54px; height: 54px; border-radius: 50%;
    background: var(--blue-mid);
  }
  .brand-name {
    font-weight: 700; font-size: 44px; color: var(--blue-deep);
    letter-spacing: 0.5px;
  }

  .card-front .brand {
    position: absolute; left: 0; right: 0; top: 150px; justify-content: center;
  }
  .front-web {
    position: absolute; left: 0; right: 0; top: 300px; text-align: center;
    font-size: 19px; letter-spacing: 4px; color: var(--ink);
  }

  .card-back .brand {
    position: absolute; left: 60px; top: 160px;
  }
  .card-back .brand-name { font-size: 40px; }
  .divider {
    position: absolute; left: 395px; top: 50px; width: 1px; height: 250px;
    background: var(--rule);
  }
  .contact {
    position: absolute; left: 425px; top: 52px; width: 260px;
    color: var(--ink);
  }
  .contact-name {
    font-size: 21px; font-weight: 700; color: var(--blue-deep); line-height: 1.2;
  }
  .contact-title {
    font-size: 17px; color: var(--ink-soft); margin: 4px 0 12px 6px;
  }
  .contact-list { list-style: none; }
  .contact-list li {
    display: flex; align-items: center; gap: 8px;
    font-size: 15.5px; line-height: 1.65; padding-left: 14px;
  }
  .contact-list svg { width: 14px; height: 14px; flex: none; }
  .contact-address {
    font-size: 15.5px; line-height: 1.35; padding-left: 36px; margin-top: 6px;
  }
  .band { position: absolute; left: 0; bottom: 0; width: 700px; height: 90px; }
</style>
</head>
<body>
<div class="canvas">

  <section class="card card-front">
    <div class="brand">
      <span class="brand-mark"></span>
      <span class="brand-name">Velbrantix</span>
    </div>
    <p class="front-web">www.velbrantix.com</p>
  </section>

  <section class="card card-back">
    <div class="brand">
      <span class="brand-mark"></span>
      <span class="brand-name">Velbrantix</span>
    </div>

    <div class="divider"></div>

    <div class="contact">
      <h2 class="contact-name">Your Name</h2>
      <p class="contact-title">Title</p>
      <ul class="contact-list">
        <li>
          <svg viewBox="0 0 14 14"><path fill="#0792cd" d="M3 1l2 3-1.3 1.3a8 8 0 0 0 5 5L10 9l3 2-1 2.5C6 13 1 8 0.5 2z"/></svg>
          012-345-6789
        </li>
        <li>
          <svg viewBox="0 0 14 14"><rect x="3.5" y="0.5" width="7" height="13" rx="1.2" fill="#0792cd"/><rect x="5" y="2.5" width="4" height="6" fill="#fff"/></svg>
          012-345-6789
        </li>
        <li>
          <svg viewBox="0 0 14 14"><rect x="0.5" y="3" width="13" height="9" rx="1" fill="#0792cd"/><path d="M1 3.5l6 4.5 6-4.5" stroke="#fff" stroke-width="1.2" fill="none"/></svg>
          info@velbrantix.com
        </li>
        <li>
          <svg viewBox="0 0 14 14"><circle cx="7" cy="7" r="6.2" fill="#0792cd"/><path d="M1 7h12M7 1c-3 3-3 9 0 12M7 1c3 3 3 9 0 12" stroke="#fff" stroke-width="0.9" fill="none"/></svg>
          www.velbrantix.com
        </li>
      </ul>
      <p class="contact-address">Street Name, City Name<br>Zipcode-012345</p>
    </div>

    <svg class="band" viewBox="0 0 700 90" preserveAspectRatio="none" aria-hidden="true">
      <polygon points="0,74 700,74 700,90 0,90" fill="#0792cd"/>
      <polygon points="345,74 365,58 700,58 700,74" fill="#33a6d7"/>
      <polygon points="330,74 350,58 358,58 338,74" fill="#33a6d7"/>
    </svg>
  </section>

</div>
</body>
</html>
```